Velk Partners Building Business Cards

We need a business card that reflects our business as "Solar Experts" in San Diego. Browse our website www.velkpartners.example our License needs to be displayed as "CSLB# 3867140" our phone number is (619) 555-0187

Save thousands on your electric bills and increase the value of your home while helping to protect the environment. Our solar installation experts will help you design the system that's right for you, using only the highest quality equipment that will look great and give you ideal performance. Our goal is to make you energy independent, and get your electric bill to 0.

Paul Osterby
(619) 555-0187
paul@velkpartners.example

Target Market(s)

Home owners in san diego looking for solar

Industry/Entity Type

Solar Energy

Contact Information for Business Card

Paul Osterby
(619) 555-0187
paul@velkpartners.example

Font styles to use
Other font styles liked:
• Use our logo font

Requirements
Must have
• License needs to be displayed as "CSLB# 3867140" our phone number is (619) 555-0187
Nice to have
• Real images of rooftop home solar in san diego
Should not have
• our business address

```html
<!DOCTYPE html>
<html lang="en">
<head>
<meta charset="utf-8">
<title>Velk Partners Building – Business Card</title>
<link href="https://fonts.googleapis.com/css2?family=Roboto:wght@400;500;700&display=swap" rel="stylesheet">
<style>
  :root {
    --page-bg: #e4ddd5;
    --card-bg: #f3f1ee;
    --card-edge: #d6d1cb;
    --navy: #2b3e6b;
    --gold: #e0a21f;
    --ink: #2f3d5c;
  }
  html, body {
    margin: 0;
    padding: 0;
    width: 1200px;
    height: 1200px;
    overflow: hidden;
    background: var(--page-bg);
    font-family: "Roboto", Arial, sans-serif;
  }
  .canvas {
    position: relative;
    width: 1200px;
    height: 1200px;
  }
  .card {
    position: absolute;
    left: 170px;
    top: 370px;
    width: 860px;
    height: 510px;
    background: var(--card-bg);
    border: 1px solid var(--card-edge);
    box-sizing: border-box;
    box-shadow: 0 10px 30px rgba(60, 45, 30, 0.12);
  }
  .brand {
    position: absolute;
    left: 58px;
    top: 80px;
    margin: 0;
    color: var(--navy);
    font-weight: 700;
    font-size: 46px;
    line-height: 1.1;
    letter-spacing: -0.5px;
  }
  .person {
    position: absolute;
    left: 58px;
    top: 285px;
  }
  .person-name {
    margin: 0;
    color: var(--navy);
    font-weight: 700;
    font-size: 29px;
  }
  .person-title {
    margin: 8px 0 0;
    color: var(--ink);
    font-size: 20px;
  }
  .contact {
    position: absolute;
    left: 455px;
    top: 287px;
    margin: 0;
    padding: 0;
    list-style: none;
    color: var(--ink);
    font-size: 21px;
  }
  .contact-item {
    display: flex;
    align-items: center;
    height: 30px;
  }
  .contact-icon {
    width: 22px;
    height: 22px;
    margin-right: 21px;
    flex: none;
  }
  .contact-web .accent { color: var(--gold); }
  .license {
    margin-top: 10px;
    margin-left: -12px;
  }
</style>
</head>
<body>
<main class="canvas">
  <section class="card" aria-label="Business card">
    <h1 class="brand">Velk Partners Building Inc</h1>

    <div class="person">
      <p class="person-name">Paul Osterby</p>
      <p class="person-title">Managing Director</p>
    </div>

    <ul class="contact">
      <li class="contact-item">
        <svg class="contact-icon" viewBox="0 0 24 24" aria-hidden="true">
          <path fill="#e0a21f" d="M4 9c0-3 4-5 8-5s8 2 8 5v2h-4V9H8v2H4z"/>
          <rect fill="#e0a21f" x="5" y="12" width="14" height="8" rx="1.5"/>
          <circle fill="#f3f1ee" cx="12" cy="16" r="2.2"/>
        </svg>
        <span>(619) 555-0187</span>
      </li>
      <li class="contact-item">
        <svg class="contact-icon" viewBox="0 0 24 24" aria-hidden="true">
          <circle cx="12" cy="12" r="9" fill="#e0a21f"/>
          <g fill="none" stroke="#f3f1ee" stroke-width="1.3">
            <ellipse cx="12" cy="12" rx="4" ry="9"/>
            <line x1="3" y1="12" x2="21" y2="12"/>
            <line x1="12" y1="3" x2="12" y2="21"/>
          </g>
        </svg>
        <span>paul@velkpartners.example</span>
      </li>
      <li class="contact-item contact-web">
        <svg class="contact-icon" viewBox="0 0 24 24" aria-hidden="true">
          <rect x="2" y="5" width="20" height="14" rx="1" fill="#e0a21f"/>
          <path d="M2.5 6 12 13.5 21.5 6" fill="none" stroke="#f3f1ee" stroke-width="1.4"/>
        </svg>
        <span>www.<span class="accent">velkpartners</span>.example</span>
      </li>
      <li class="contact-item license">
        <span>License: CSLB# 3867140</span>
      </li>
    </ul>
  </section>
</main>
</body>
</html>
```